Corvana Tongue Works, LLC

We need a business card that includes information about our business and conveys a reliable business that provides document translation services and interpreters for a variety of corporate and individual clients. We want to come across as professional, reliable, yet approachable. It should include the following on one side:

ESL / ENL Language Classes, Private Lessons, and Online Tutors
PLEXA Training and Testing
Translating & Interpreting Services
Contact us about Over-the-Phone Interpreting in over 200 languages
24/7/365
www.corvanatongue.example

The other side should include (555) 481-3062

Rhoda Pelling, President
482 Garnet Ave., Ste. 219
Indianapolis, IN 40917

Please add USA as part of the address. Also, please add rmpelling@corvanatongueworks.example as the e-mail address. Thank you.

Target Market(s)

Business professionals, their families, the international community

Industry/Entity Type

Business

Contact Information for Business Card

24/7/365
www.corvanatongue.example

(555) 481-3062

Rhoda Pelling, President
482 Garnet Ave., Ste. 219
Indianapolis, IN 40917
USA

Font styles to use
Sans Serif

Colors

Designer to choose colors to be used in the design.

Requirements
Must have
• See project description
• e-mail address and web address
• Phone number
Nice to have
• a globe
• physical address
Should not have
• Should not have the same color scheme as other agencies in our market in Indiana unless it is blue and black. No purple or yellow.

```html
<!DOCTYPE html>
<html lang="en">
<head>
<meta charset="utf-8">
<title>Corvana Tongue Works — Business Card</title>
<link href="https://fonts.googleapis.com/css2?family=Work+Sans:wght@400;500&display=swap" rel="stylesheet">
<style>
  :root {
    --backdrop: #2a2a2b;
    --card: #1b1b1c;
    --ink: #dcdcdc;
    --ink-soft: #b9b9b9;
    --emboss: #3b3b3c;
    --rule: #8a8a8a;
  }
  * { margin: 0; padding: 0; box-sizing: border-box; }
  html, body { width: 1200px; height: 900px; overflow: hidden; }
  body {
    background: var(--backdrop);
    font-family: "Work Sans", Arial, sans-serif;
    position: relative;
  }
  .card {
    position: absolute;
    left: 240px;
    width: 720px;
    height: 400px;
    background: var(--card);
    box-shadow: 0 10px 30px rgba(0,0,0,.45);
    overflow: hidden;
  }
  .card--front { top: 35px; }
  .card--back { top: 465px; }

  /* Brand lockup */
  .brand { display: flex; align-items: center; }
  .brand__dot {
    border-radius: 50%;
    border: 3px solid currentColor;
    flex: none;
  }
  .brand__name {
    font-weight: 400;
    line-height: 1.05;
    white-space: nowrap;
  }

  /* Front */
  .card--front .brand {
    position: absolute; left: 215px; top: 40px; gap: 18px;
    color: var(--ink-soft);
  }
  .card--front .brand__dot { width: 96px; height: 96px; }
  .card--front .brand__name { font-size: 34px; }
  .services {
    position: absolute; left: 0; right: 0; top: 188px;
    text-align: center; color: var(--ink-soft);
    font-size: 16px; line-height: 1.45;
  }
  .services__rule {
    width: 560px; height: 1px; background: var(--rule);
    margin: 8px auto 8px;
  }
  .services__hours, .services__web { color: var(--ink); }

  /* Back */
  .card--back .brand {
    position: absolute; left: 36px; top: 140px; gap: 14px;
    color: var(--emboss);
  }
  .card--back .brand__dot { width: 80px; height: 80px; }
  .card--back .brand__name { font-size: 28px; }
  .divider {
    position: absolute; left: 310px; top: 80px;
    width: 2px; height: 240px; background: var(--emboss);
  }
  .contact {
    position: absolute; left: 338px; top: 78px;
    color: var(--ink);
  }
  .contact__name { font-size: 32px; font-weight: 500; letter-spacing: .5px; }
  .contact__title { font-size: 17px; color: var(--ink-soft); margin-bottom: 20px; }
  .contact__address { font-size: 17px; line-height: 1.4; margin-bottom: 14px; }
  .contact__line {
    display: flex; align-items: center; gap: 10px;
    font-size: 16px; line-height: 1.6; white-space: nowrap;
  }
  .contact__line svg { width: 12px; height: 12px; flex: none; }
</style>
</head>
<body>

  <section class="card card--front">
    <div class="brand">
      <span class="brand__dot"></span>
      <span class="brand__name">Corvana<br>Tongue<br>Works, LLC</span>
    </div>
    <div class="services">
      <p>ESL / ENL Language Classes, Private Lessons, and Online Tutors</p>
      <p>PLEXA Training and Testing</p>
      <p>Translating &amp; Interpreting Services</p>
      <div class="services__rule"></div>
      <p>Contact us about Over-the-Phone Interpreting in over 200 languages</p>
      <p class="services__hours">24/7/365</p>
      <p class="services__web">www.corvanatongue.example</p>
    </div>
  </section>

  <section class="card card--back">
    <div class="brand">
      <span class="brand__dot"></span>
      <span class="brand__name">Corvana<br>Tongue<br>Works, LLC</span>
    </div>
    <div class="divider"></div>
    <div class="contact">
      <h1 class="contact__name">RHODA PELLING</h1>
      <p class="contact__title">President</p>
      <p class="contact__address">482 Garnet Ave., Ste. 219<br>Indianapolis, IN 40917 USA</p>
      <p class="contact__line">
        <svg viewBox="0 0 12 12"><path d="M2.5 1h2l1 2.5-1.3 1a6 6 0 0 0 3.3 3.3l1-1.3L11 7.5v2A1.5 1.5 0 0 1 9.5 11 8.5 8.5 0 0 1 1 2.5 1.5 1.5 0 0 1 2.5 1z" fill="#dcdcdc"/></svg>
        (555) 481-3062
      </p>
      <p class="contact__line">
        <svg viewBox="0 0 12 12"><rect x="1" y="2.5" width="10" height="7" fill="none" stroke="#dcdcdc" stroke-width="1.2"/><path d="M1 2.5l5 4 5-4" fill="none" stroke="#dcdcdc" stroke-width="1.2"/></svg>
        rmpelling@corvanatongueworks.example
      </p>
      <p class="contact__line">
        <svg viewBox="0 0 12 12"><circle cx="6" cy="6" r="5" fill="none" stroke="#dcdcdc" stroke-width="1.1"/><ellipse cx="6" cy="6" rx="2.2" ry="5" fill="none" stroke="#dcdcdc" stroke-width="1"/><path d="M1 6h10" stroke="#dcdcdc" stroke-width="1"/></svg>
        www.corvanatongue.example
      </p>
    </div>
  </section>

</body>
</html>
```